business card

Business card for new business.
Red and black corporate colors.
Card can have an Indsutrial feel to it. Feel free to add Rust, Bolted steel, or graphics as you see fit. We provide highly specialized services to the below mentioned industries.
Keep information out of corners so that if I want I can choose rounded corners.
Information
- front. name - title - phone - email
- Rear
Welding - Piping - Fabrication - Rigging - Utilities
Northgate - Eastbrook - Pine Ridge Falls - Lakeshore - Westfield

```html
<!DOCTYPE html>
<html lang="en">
<head>
<meta charset="utf-8">
<title>Ironvale business card</title>
<link rel="stylesheet" href="https://fonts.googleapis.com/css2?family=Source+Sans+3:wght@400;600;700;900&display=swap">
<style>
  :root {
    --backdrop: #2b2b2c;
    --card: #1f2021;
    --red: #e3001b;
    --white: #f2f2f2;
    --grey: #8a8a8a;
    --steel-light: #e6e6e6;
    --steel-dark: #3a3a3a;
  }
  * { margin: 0; padding: 0; box-sizing: border-box; }
  html, body { width: 1200px; height: 960px; overflow: hidden; }
  body {
    background: var(--backdrop);
    font-family: "Source Sans 3", "Helvetica Neue", Arial, sans-serif;
    position: relative;
  }
  .card {
    position: absolute;
    width: 600px;
    height: 342px;
    background: var(--card);
    box-shadow: 0 6px 14px rgba(0,0,0,0.45);
  }
  .card--front { left: 303px; top: 125px; }
  .card--back  { left: 300px; top: 493px; width: 598px; }

  .brand-panel {
    position: absolute;
    left: 46px; top: 37px;
    width: 162px; height: 276px;
    background: linear-gradient(160deg, var(--steel-light) 0%, #9d9d9d 55%, var(--steel-dark) 100%);
    display: flex; align-items: center; justify-content: center;
  }
  .brand-panel__name {
    writing-mode: vertical-rl;
    transform: rotate(180deg);
    font-weight: 900;
    font-size: 40px;
    letter-spacing: 4px;
    color: var(--card);
  }

  .contact {
    position: absolute;
    right: 62px; top: 172px;
    text-align: right;
  }
  .contact__name {
    color: var(--red);
    font-weight: 600;
    font-size: 21px;
    line-height: 24px;
  }
  .contact__title {
    color: var(--grey);
    font-size: 15px;
    line-height: 18px;
    margin-bottom: 8px;
  }
  .contact__line {
    color: var(--white);
    font-size: 15px;
    line-height: 19.5px;
    display: flex; align-items: center; justify-content: flex-end; gap: 6px;
  }
  .contact__icon { width: 13px; height: 13px; fill: var(--red); flex: none; margin-right: -1px; }

  .wordmark {
    position: absolute;
    left: 0; right: 0; top: 138px;
    display: flex; align-items: center; justify-content: center; gap: 12px;
  }
  .wordmark__square { width: 22px; height: 22px; background: var(--red); }
  .wordmark__name {
    font-weight: 900;
    font-size: 50px;
    line-height: 1;
    color: var(--grey);
    letter-spacing: 1px;
  }
  .services {
    position: absolute;
    left: 0; right: 0; top: 256px;
    text-align: center;
    color: var(--white);
    font-size: 15.5px;
    line-height: 19.5px;
  }
  .services__dot { color: var(--red); font-size: 14px; padding: 0 1px 0 2px; }
</style>
</head>
<body>
  <section class="card card--front">
    <div class="brand-panel">
      <span class="brand-panel__name">IRONVALE</span>
    </div>
    <div class="contact">
      <div class="contact__name">MARK ELLIS</div>
      <div class="contact__title">PRESIDENT</div>
      <div class="contact__line">555 0142 7781
        <svg class="contact__icon" viewBox="0 0 16 16"><path d="M3 5c0-2 2-3 5-3s5 1 5 3v1h-3V5H6v1H3z"/><rect x="3" y="8" width="10" height="6" rx="1"/></svg>
      </div>
      <div class="contact__line">mark@ironvale.com
        <svg class="contact__icon" viewBox="0 0 16 16"><path d="M1 4h14v1L8 9 1 5z"/><path d="M1 6.5l7 4 7-4V12H1z"/></svg>
      </div>
      <div class="contact__line">www.ironvale.com
        <svg class="contact__icon" viewBox="0 0 16 16"><circle cx="8" cy="8" r="7"/><path d="M4 5h4v3H5zM9 9h3l-1 3H9z" fill="#1f2021"/></svg>
      </div>
    </div>
  </section>

  <section class="card card--back">
    <div class="wordmark">
      <span class="wordmark__square"></span>
      <span class="wordmark__name">IRONVALE</span>
    </div>
    <div class="services">
      Welding <span class="services__dot">&bull;</span>Piping <span class="services__dot">&bull;</span>Fabrication <span class="services__dot">&bull;</span>Rigging<br>
      Utilities <span class="services__dot">&bull;</span>Northgate <span class="services__dot">&bull;</span>Eastbrook <span class="services__dot">&bull;</span>Pine Ridge Falls<br>
      Lakeshore <span class="services__dot">&bull;</span>Westfield
    </div>
  </section>
</body>
</html>
```